R7M Horizon Business Card Design

We need a business card created for our New Business "R7M Horizon"<br/><br/>The business card design is up to you however the following information must be on the business card:<br/><br/>Front of the business card -<br/>Email :darrenp@r7mhorizon.nz<br/>Mobile: +64 (0) 22 4870 619<br/>Website: www.r7mhorizon.nz<br/>Card Owner Name: Darren Paltrow<br/>Company Title: Business Development Manager<br/>Slogan: "The BEST of both worlds". <br/>Logo On the front attached to the design brief<br/><br/>On the back: <br/>Space on the back for 4 more versions of the logo across the bottom of the card indicating different subsidiary brands - R7M Coffee, R7M Arts, R7M ?? (The card will be used for all of these brands - We Will add the extra subsidiary logos to the design once the design is finished (We are a graphics design team). <br/><br/>Other than that we want a premium feeling logo that remains universally usable depending on the business entity that we are using the card for. The use of bright bold colours would be great but we still want the card to feel premium.
Target Market(s)
Gift Design and Manufacturing Companies
Contact Information for Business Card
Front of the business card -
Email :darrenp@r7mhorizon.nz
Mobile: +64 (0) 22 4870 619
Website: www.r7mhorizon.nz
Card Owner Name: Darren Paltrow
Company Title: Business Development Manager
Slogan: "The BEST of both worlds".
Logo On the front attached to the design brief

```html
<!DOCTYPE html>
<html lang="en">
<head>
<meta charset="utf-8">
<title>R7M Horizon Business Card</title>
<link href="https://fonts.googleapis.com/css2?family=Orbitron:wght@800&family=Open+Sans:wght@400;600&family=Exo+2:ital,wght@1,400;1,700&display=swap" rel="stylesheet">
<style>
  :root {
    --backdrop: #d2d7d7;
    --card-white: #efefec;
    --brand-blue: #2d3ea3;
    --ink-grey: #4a4a4a;
    --shadow: rgba(40, 50, 60, 0.22);
  }
  html, body {
    margin: 0;
    padding: 0;
    width: 1200px;
    height: 900px;
    overflow: hidden;
    background: var(--backdrop);
  }
  .canvas {
    width: 1200px;
    height: 900px;
    display: flex;
    flex-direction: column;
    align-items: center;
    justify-content: center;
    gap: 36px;
  }
  .card {
    position: relative;
    width: 700px;
    height: 400px;
    box-shadow: 0 14px 30px var(--shadow);
  }
  .card--front { background: var(--card-white); }
  .card--back {
    background: var(--brand-blue);
    display: flex;
    align-items: center;
    justify-content: center;
  }

  .identity {
    position: absolute;
    right: 372px;
    top: 150px;
    text-align: right;
  }
  .identity__name {
    font-family: "Orbitron", sans-serif;
    font-weight: 800;
    font-size: 25px;
    letter-spacing: 1.5px;
    color: var(--brand-blue);
    text-transform: uppercase;
    margin: 0;
    line-height: 1.1;
    white-space: nowrap;
  }
  .identity__role {
    font-family: "Open Sans", sans-serif;
    font-size: 17px;
    color: var(--ink-grey);
    margin: 4px 0 0;
    white-space: nowrap;
  }
  .divider {
    position: absolute;
    left: 348px;
    top: 150px;
    width: 2px;
    height: 88px;
    background: var(--brand-blue);
  }
  .contacts {
    position: absolute;
    left: 374px;
    top: 150px;
    list-style: none;
    margin: 0;
    padding: 0;
    font-family: "Open Sans", sans-serif;
    font-size: 17px;
    color: var(--ink-grey);
  }
  .contacts__item {
    display: flex;
    align-items: center;
    gap: 10px;
    height: 29px;
    white-space: nowrap;
  }
  .contacts__icon { width: 14px; height: 14px; flex: none; }
  .slogan {
    position: absolute;
    left: 0;
    width: 540px;
    top: 300px;
    text-align: center;
    font-family: "Exo 2", sans-serif;
    font-style: italic;
    font-size: 19px;
    color: var(--brand-blue);
    margin: 0;
  }
  .slogan strong { font-weight: 700; }

  .brand-name {
    font-family: "Open Sans", sans-serif;
    font-weight: 600;
    font-size: 48px;
    letter-spacing: 1px;
    color: var(--card-white);
    margin: 0;
    white-space: nowrap;
  }
</style>
</head>
<body>
<main class="canvas">
  <section class="card card--front" aria-label="Business card front">
    <div class="identity">
      <h1 class="identity__name">Darren Paltrow</h1>
      <p class="identity__role">Business Development Manager</p>
    </div>
    <div class="divider"></div>
    <ul class="contacts">
      <li class="contacts__item">
        <svg class="contacts__icon" viewBox="0 0 14 14" aria-hidden="true"><path d="M3 1 L5.5 1 L6.5 4 L5 5.2 Q6.2 8 8.8 9 L10 7.5 L13 8.5 L13 11 Q12.5 13 10.5 13 Q2 12 1 3.5 Q1 1.2 3 1 Z" fill="var(--brand-blue)"/></svg>
        <span>+64 (0) 22 4870 619</span>
      </li>
      <li class="contacts__item">
        <svg class="contacts__icon" viewBox="0 0 14 14" aria-hidden="true"><rect x="1" y="3" width="12" height="8.5" fill="none" stroke="var(--brand-blue)" stroke-width="1.4"/><path d="M1 3.5 L7 8 L13 3.5" fill="none" stroke="var(--brand-blue)" stroke-width="1.4"/></svg>
        <span>darrenp@r7mhorizon.nz</span>
      </li>
      <li class="contacts__item">
        <svg class="contacts__icon" viewBox="0 0 14 14" aria-hidden="true"><circle cx="7" cy="7" r="6" fill="var(--brand-blue)"/><path d="M1 7 H13 M7 1 V13 M2.5 4 H11.5 M2.5 10 H11.5" stroke="var(--card-white)" stroke-width="0.8"/><ellipse cx="7" cy="7" rx="2.6" ry="6" fill="none" stroke="var(--card-white)" stroke-width="0.8"/></svg>
        <span>www.r7mhorizon.nz</span>
      </li>
    </ul>
    <p class="slogan">The <strong>BEST</strong> of both worlds</p>
  </section>

  <section class="card card--back" aria-label="Business card back">
    <p class="brand-name">R7M Horizon</p>
  </section>
</main>
</body>
</html>
```